Design for a 4 screens iOS and Android app - "VelaTrakko"

The app allows you to track your car gasoline refill ...
We need a design for the 4 screens of the app:
a) 1 form with 3 fields.
b) 1 simple list view
c) 1 summary view
d) 1 text page
2 "alerts" items are also to be designed.
No specific guidelines, nor logo or whatever.
It will be a free app distributed on iOS and Androïd.
We just want to make it looking nice & very usable for end users.
Target Market(s)
B2C app
Industry/Entity Type
Android

```html
<!DOCTYPE html>
<html lang="fr">
<head>
<meta charset="utf-8">
<title>VelaTrakko – Statistics</title>
<link href="https://fonts.googleapis.com/css2?family=Roboto:wght@400;500&display=swap" rel="stylesheet">
<style>
  :root {
    --status-bg: #0f3447;
    --appbar-bg: #1c6587;
    --on-bar: #ffffff;
    --on-bar-muted: rgba(255,255,255,0.85);
    --surface: #ffffff;
    --divider: #dddddd;
    --heading: #212121;
    --label: #bdbdbd;
    --value: #666666;
    --nav-bg: #000000;
    --nav-icon: #ffffff;
  }
  * { margin: 0; padding: 0; box-sizing: border-box; }
  html, body { width: 675px; height: 1200px; overflow: hidden; }
  body {
    font-family: 'Roboto', Arial, sans-serif;
    background: var(--surface);
    position: relative;
  }
  .status-bar {
    position: absolute; left: 0; top: 0; width: 675px; height: 45px;
    background: var(--status-bg);
  }
  .status-bar svg { position: absolute; top: 0; }
  .status-time {
    position: absolute; right: 14px; top: 0; line-height: 45px;
    color: var(--on-bar); font-size: 21px;
  }
  .app-bar {
    position: absolute; left: 0; top: 45px; width: 675px; height: 171px;
    background: var(--appbar-bg);
    box-shadow: 0 3px 5px rgba(0,0,0,0.25);
    z-index: 2;
  }
  .back-button { position: absolute; left: 31px; top: 27px; }
  .app-title {
    position: absolute; left: 138px; top: 22px;
    color: var(--on-bar); font-size: 35px; font-weight: 400; line-height: 44px;
  }
  .tabs { position: absolute; left: 0; top: 110px; width: 675px; height: 61px; display: flex; }
  .tab {
    flex: 1; text-align: center; color: var(--on-bar-muted);
    font-size: 20.5px; line-height: 36px; text-transform: uppercase;
  }
  .tab.is-active { color: var(--on-bar); }
  .tab-indicator {
    position: absolute; left: 0; bottom: 0; width: 337.5px; height: 4px;
    background: var(--on-bar);
  }
  .month-heading {
    position: absolute; left: 45px; font-size: 32px; font-weight: 400;
    color: var(--heading); line-height: 40px;
  }
  .divider { position: absolute; left: 0; width: 675px; height: 1.5px; background: var(--divider); }
  .stat-row {
    position: absolute; left: 50px; right: 37px; display: flex;
    justify-content: space-between; font-size: 24.5px; line-height: 32px;
  }
  .stat-label { color: var(--label); }
  .stat-value { color: var(--value); }
  .nav-bar {
    position: absolute; left: 0; top: 1114px; width: 675px; height: 86px;
    background: var(--nav-bg);
  }
  .nav-bar svg { position: absolute; top: 27px; }
</style>
</head>
<body>
  <div class="status-bar">
    <svg style="left:451px" width="22" height="45" viewBox="0 0 22 45"><path d="M11 12c-4.4 0-8 3.4-8 7.7 0 5.6 8 13.3 8 13.3s8-7.7 8-13.3C19 15.4 15.4 12 11 12zm0 10.5a3 3 0 1 1 0-6 3 3 0 0 1 0 6z" fill="#fff"/></svg>
    <svg style="left:485px" width="36" height="45" viewBox="0 0 36 45"><path d="M18 34 1 15c9.5-8 24.5-8 34 0z" fill="#fff"/></svg>
    <svg style="left:523px" width="28" height="45" viewBox="0 0 28 45"><path d="M2 34 26 10v24z" fill="#fff"/></svg>
    <svg style="left:565px" width="18" height="45" viewBox="0 0 18 45"><rect x="5" y="9" width="8" height="3" fill="#fff"/><rect x="2" y="11" width="14" height="23" rx="1" fill="#fff"/></svg>
    <span class="status-time">10:55</span>
  </div>

  <header class="app-bar">
    <svg class="back-button" width="34" height="34" viewBox="0 0 24 24" aria-label="Back"><path d="M20 11H7.8l5.6-5.6L12 4l-8 8 8 8 1.4-1.4L7.8 13H20z" fill="#fff"/></svg>
    <h1 class="app-title">Statistics</h1>
    <nav class="tabs">
      <span class="tab is-active">Summary</span>
      <span class="tab">List</span>
      <span class="tab-indicator"></span>
    </nav>
  </header>

  <main class="summary">
    <h2 class="month-heading" style="top:257px">Février 2016</h2>
    <div class="divider" style="top:337px"></div>
    <div class="stat-row" style="top:374px"><span class="stat-label">Total cost</span><span class="stat-value">570.54 €</span></div>
    <div class="stat-row" style="top:457px"><span class="stat-label">Mileage</span><span class="stat-value">7500 km</span></div>
    <div class="stat-row" style="top:541px"><span class="stat-label">Full tanks</span><span class="stat-value">11</span></div>
    <div class="stat-row" style="top:625px"><span class="stat-label">Consumption</span><span class="stat-value">6.5 l</span></div>
    <div class="divider" style="top:708px"></div>

    <h2 class="month-heading" style="top:748px">Janvier 2016</h2>
    <div class="divider" style="top:828px"></div>
    <div class="stat-row" style="top:874px"><span class="stat-label">Total cost</span><span class="stat-value">570.54 €</span></div>
    <div class="stat-row" style="top:957px"><span class="stat-label">Mileage</span><span class="stat-value">7500 km</span></div>
  </main>

  <div class="nav-bar">
    <svg style="left:134px" width="32" height="32" viewBox="0 0 32 32" aria-label="Back"><path d="M27 3v26L4 16z" fill="none" stroke="#fff" stroke-width="3" stroke-linejoin="round"/></svg>
    <svg style="left:321px" width="32" height="32" viewBox="0 0 32 32" aria-label="Home"><circle cx="16" cy="16" r="13.5" fill="none" stroke="#fff" stroke-width="3"/></svg>
    <svg style="left:511px" width="32" height="32" viewBox="0 0 32 32" aria-label="Recent apps"><rect x="3" y="3" width="26" height="26" rx="1.5" fill="none" stroke="#fff" stroke-width="3"/></svg>
  </div>
</body>
</html>
```